Business Card Design

We would like to re-design our business cards. Our Company - Qwinrel Turbochargers, rebuilds turbochargers and sells replacement parts. Our website is: http://www.qwinrelturbochargers-example.com
We just had our logo changed. I will attach the file. Looking for fresh new/modern business card. We like the colors red, black, white and silver. Black background looks attractive, but not a requirement. The final design should communicate reasonable/competitive prices, top quality and reliability of our products.
Updates
Project Deadline Extended
Reason: Need to finalize the info on the card. Currently working on changing address and email info. Want to make sure it is the correct one before accepting the final design. Unless, this is something that can be changed at a later time..??
Industry/Entity Type
Business
Contact Information for Business Card
QWINREL TURBOCHARGERS, LLC
20473 Harwick Lane NE
Massillon, OH 44647
Tel: +1-555-214-7390
Fax: +1-555-267-1842
info@QwinrelTurbochargers-example.com
Our current business card had the following highlights:
*We rebuild all Turbocharges for Automotive, Diesel and Industrial
*Precision Balancing and in-house turbocharger needs
*All Turbocharger replacement parts are made in USA / U.K.
Look and feel
Each slider illustrates characteristics of the customer's brand and the style your logo design should communicate.

```html
<!DOCTYPE html>
<html lang="en">
<head>
<meta charset="utf-8">
<title>Qwinrel Turbochargers – Business Card</title>
<link href="https://fonts.googleapis.com/css2?family=Source+Sans+3:wght@400;600;800&display=swap" rel="stylesheet">
<style>
  :root {
    --bg: #232323;
    --red: #e3262f;
    --red-dark: #c81e26;
    --black: #161616;
    --white: #f7f7f7;
    --grey: #3a3a3a;
  }
  * { box-sizing: border-box; margin: 0; padding: 0; }
  html, body { width: 1200px; height: 900px; overflow: hidden; }
  body {
    background: var(--bg);
    font-family: "Source Sans 3", Arial, sans-serif;
    position: relative;
  }
  .card {
    position: absolute;
    width: 560px;
    height: 320px;
    border-radius: 4px;
    overflow: hidden;
  }
  .card-front {
    left: 60px; top: 90px;
    background: linear-gradient(135deg, var(--red-dark), var(--red));
    display: flex; align-items: center; justify-content: center;
  }
  .brand {
    display: flex; align-items: center; gap: 12px;
    font-weight: 800; font-size: 34px; letter-spacing: 0.5px;
  }
  .brand-dot { width: 22px; height: 22px; border-radius: 50%; }
  .card-front .brand { color: var(--black); }
  .card-front .brand-dot { background: var(--black); }

  .card-back {
    left: 580px; top: 490px;
    background: var(--white);
  }
  .card-back .brand {
    position: absolute; left: 170px; top: 34px;
    font-size: 28px; color: var(--black);
  }
  .card-back .brand-dot { background: var(--red); width: 18px; height: 18px; }
  .person { position: absolute; left: 34px; top: 92px; }
  .person-name { color: var(--red); font-size: 22px; font-weight: 400; line-height: 1; }
  .person-role { color: var(--grey); font-size: 14px; margin-top: 2px; }
  .rule {
    position: absolute; left: 108px; right: 0; top: 128px;
    height: 1.5px; background: var(--red);
  }
  .contacts {
    position: absolute; left: 30px; top: 146px;
    list-style: none; font-size: 15px; color: var(--black); line-height: 21px;
  }
  .contacts li { display: flex; align-items: center; gap: 8px; }
  .contacts svg { width: 12px; height: 12px; fill: var(--red); flex: none; }
  .address-band {
    position: absolute; left: 0; right: 0; bottom: 0; height: 60px;
    background: linear-gradient(180deg, var(--red), var(--red-dark));
    border-radius: 24px 24px 0 0;
    color: var(--white); font-size: 19px;
    display: flex; align-items: center; padding-left: 34px;
  }
</style>
</head>
<body>
  <section class="card card-front">
    <div class="brand"><span class="brand-dot"></span>Qwinrel Turbochargers</div>
  </section>

  <section class="card card-back">
    <div class="brand"><span class="brand-dot"></span>Qwinrel Turbochargers</div>
    <div class="person">
      <p class="person-name">Marlon Tegwick</p>
      <p class="person-role">Director</p>
    </div>
    <div class="rule"></div>
    <ul class="contacts">
      <li><svg viewBox="0 0 12 12"><path d="M2.5 0.5l2 2.5-1.2 1.2c.8 1.7 2 2.9 3.5 3.5L8 6.5l2.5 2-1 2.5C5 11 1 7 1 1.5z"/></svg>+1-555-214-7390</li>
      <li><svg viewBox="0 0 12 12"><rect x="3" y="0.5" width="6" height="3"/><rect x="0.5" y="4" width="11" height="5" rx="1"/><rect x="3" y="8" width="6" height="3.5"/></svg>+1-555-267-1842</li>
      <li><svg viewBox="0 0 12 12"><path d="M0.5 2h11v8h-11z M1.5 3l4.5 3.5L10.5 3" stroke="#fff" stroke-width="1"/></svg>info@QwinrelTurbochargers-example.com</li>
      <li><svg viewBox="0 0 12 12"><circle cx="6" cy="6" r="5.5"/><path d="M0.5 6h11M6 0.5v11M2 3h8M2 9h8" stroke="#fff" stroke-width="0.8" fill="none"/></svg>www.qwinrelturbochargers-example.com</li>
    </ul>
    <div class="address-band">4819 Brindle Ave. NE North Calvern. Ohio</div>
  </section>
</body>
</html>
```